Business Card Design Project

Business card based on attached logo

Todd Merrick
Todd@lorvantest.com
877-514-9073 ext. 318
Www.LorvanTest.com

Industry/Entity Type

Business

```html
<!DOCTYPE html>
<html lang="en">
<head>
<meta charset="UTF-8">
<title>LorvanTest Business Cards</title>
<link rel="stylesheet" href="https://fonts.googleapis.com/css2?family=Arimo:wght@400;700&display=swap">
<style>
  :root {
    --red: #ed1c24;
    --ink: #231f20;
    --paper: #ffffff;
    --stage: #e9e6e3;
    --muted: #9a9a9a;
  }
  * { box-sizing: border-box; margin: 0; padding: 0; }
  html, body { width: 1200px; height: 715px; overflow: hidden; }
  body {
    background: var(--stage);
    font-family: "Arimo", Arial, sans-serif;
    position: relative;
  }
  .card {
    position: absolute;
    width: 505px;
    height: 288px;
    overflow: hidden;
    box-shadow: 0 2px 6px rgba(0,0,0,0.18);
  }
  .card--front { left: 55px; top: 40px; background: var(--paper); }
  .card--back-white { left: 630px; top: 40px; background: var(--paper); }
  .card--back-red { left: 55px; top: 385px; background: var(--red); }
  .card--back-black { left: 630px; top: 385px; background: var(--ink); }

  /* Front */
  .brand {
    position: absolute;
    display: flex;
    align-items: flex-start;
    gap: 8px;
  }
  .brand__name {
    font-weight: 700;
    letter-spacing: -1px;
    line-height: 1;
  }
  .brand__mark { display: block; }
  .card--front .brand { left: 0; right: 0; top: 52px; justify-content: center; }
  .card--front .brand__name { font-size: 58px; color: var(--ink); }
  .card--front .brand__mark { width: 20px; height: 20px; background: var(--red); margin-top: -8px; }

  .holder {
    position: absolute;
    left: 86px;
    top: 223px;
    font-size: 20px;
    color: var(--red);
    letter-spacing: 1px;
  }
  .divider {
    position: absolute;
    left: 234px;
    top: 200px;
    width: 1px;
    height: 72px;
    background: linear-gradient(to bottom, rgba(0,0,0,0), var(--muted) 30%, var(--muted) 70%, rgba(0,0,0,0));
  }
  .contact {
    position: absolute;
    left: 254px;
    top: 199px;
    list-style: none;
    font-size: 14px;
    color: var(--ink);
  }
  .contact li {
    display: flex;
    align-items: center;
    gap: 7px;
    height: 24.5px;
  }
  .contact svg { width: 11px; height: 11px; fill: var(--red); flex: none; }

  /* Backs */
  .card--back-white .brand,
  .card--back-red .brand,
  .card--back-black .brand {
    left: 0; right: 0; top: 102px; justify-content: center;
  }
  .card--back-white .brand__name,
  .card--back-red .brand__name,
  .card--back-black .brand__name { font-size: 56px; }
  .card--back-white .brand__mark,
  .card--back-red .brand__mark,
  .card--back-black .brand__mark { width: 30px; height: 30px; margin-top: -14px; }

  .card--back-white .brand__name { color: var(--red); }
  .card--back-white .brand__mark { background: var(--red); }
  .card--back-red .brand__name { color: var(--paper); }
  .card--back-red .brand__mark { background: var(--paper); }
  .card--back-black .brand__name { color: var(--paper); }
  .card--back-black .brand__mark { background: var(--paper); }

  .web {
    position: absolute;
    left: 0; right: 0;
    top: 254px;
    text-align: center;
    font-size: 16px;
    letter-spacing: 3px;
  }
  .card--back-white .web { color: var(--ink); }
  .card--back-red .web,
  .card--back-black .web { color: var(--paper); }
</style>
</head>
<body>

  <section class="card card--front">
    <div class="brand">
      <span class="brand__name">LorvanTest</span>
      <span class="brand__mark"></span>
    </div>
    <p class="holder">Todd Merrick</p>
    <span class="divider"></span>
    <ul class="contact">
      <li>
        <svg viewBox="0 0 12 12" aria-hidden="true"><path d="M6 0a6 6 0 1 0 0 12A6 6 0 0 0 6 0zm0 1.3a4.7 4.7 0 1 1 0 9.4 4.7 4.7 0 0 1 0-9.4zM4.2 3.2l1 1.6-.6.6c.4.9 1 1.5 1.9 1.9l.6-.6 1.6 1-.6 1C6 8.6 3.4 6 3.2 3.8z"/></svg>
        877-514-9073 ext. 318
      </li>
      <li>
        <svg viewBox="0 0 12 12" aria-hidden="true"><path d="M0 2.5h12v7H0zm1 1v.4l5 3.1 5-3.1v-.4z"/></svg>
        Todd@lorvantest.com
      </li>
      <li>
        <svg viewBox="0 0 12 12" aria-hidden="true"><path d="M6 0a6 6 0 1 0 0 12A6 6 0 0 0 6 0zm-.6 1.1v2.2H3.5c.4-1.1 1.1-1.9 1.9-2.2zm1.2 0c.8.3 1.5 1.1 1.9 2.2H6.6zM2.3 3.3A4.9 4.9 0 0 1 3.4 1.8c-.3.4-.5.9-.7 1.5zm-.9 2.1h2c0 .4-.1.8-.1 1.2H1.3zm3.2 0h.8v1.2H4.5zm2 0h.9v1.2h-.9zm2.1 0h2l.1 1.2H8.7zM1.4 7.8h1.8c.1.6.4 1.1.6 1.6a4.8 4.8 0 0 1-2.4-1.6zm3 0h1v2.9c-.5-.5-.8-1.3-1-2.9zm2.2 0h1c-.2 1.6-.5 2.4-1 2.9zm2.2 0h1.8a4.8 4.8 0 0 1-2.4 1.6c.2-.5.5-1 .6-1.6z"/></svg>
        www.LorvanTest.com
      </li>
    </ul>
  </section>

  <section class="card card--back-white">
    <div class="brand">
      <span class="brand__name">LorvanTest</span>
      <span class="brand__mark"></span>
    </div>
    <p class="web">www.LorvanTest.com</p>
  </section>

  <section class="card card--back-red">
    <div class="brand">
      <span class="brand__name">LorvanTest</span>
      <span class="brand__mark"></span>
    </div>
    <p class="web">www.LorvanTest.com</p>
  </section>

  <section class="card card--back-black">
    <div class="brand">
      <span class="brand__name">LorvanTest</span>
      <span class="brand__mark"></span>
    </div>
    <p class="web">www.LorvanTest.com</p>
  </section>

</body>
</html>
```